Stylish business cards for KV7

To create an appealing and professional business card design for a WOMEN Owned Construction Supply Company.
2 sided card. Incorporate brand elements, curvy, colorful, sleek and bright. No solid white background. attached samples of styles added shapes/ribbons. Want something with that WOW that looks awesome, factor. It is a new logo, so feel free to mess with logo colors in the blue and teal factors that can look good with both dark and light background. If you want to try a watermark with just the KV7, without the "Supply" that might look cool to.

Industry/Entity Type

Women owned construction supply company

Contact Information for Business Card

Name, Title, and phone number and email, web page. maybe spot for qr code.

Font styles to use
Sans Serif

Requirements
Nice to have
• would love to see colors, maybe stylish ribbon dividers or some sort of 2 or 3 tone color card that compliments logo.
Should not have
• Please do not have all white background. Do not include Home/reale state/ or building images.

```html
<!DOCTYPE html>
<html lang="en">
<head>
<meta charset="utf-8">
<title>KV7 Supply — Business Cards</title>
<link rel="stylesheet" href="https://fonts.googleapis.com/css2?family=Figtree:wght@400;600;700&display=swap">
<style>
  :root {
    --stage-bg: #161718;
    --card-navy: #1c3858;
    --brand-teal: #2b95bd;
    --text-light: #e9eef3;
    --brand-white: #f4f6f8;
    --card-radius: 20px;
  }
  * { box-sizing: border-box; margin: 0; padding: 0; }
  html, body {
    width: 1200px; height: 1059px; overflow: hidden;
    background: var(--stage-bg);
    font-family: "Figtree", sans-serif;
  }
  .stage { position: relative; width: 1200px; height: 1059px; }
  .card {
    position: absolute;
    width: 690px; height: 391px;
    background: var(--card-navy);
    border-radius: var(--card-radius);
  }
  .card--front { left: 256px; top: 89px; }
  .card--back  { left: 255px; top: 548px; }

  .brand-name {
    position: absolute;
    color: var(--brand-white);
    font-weight: 700;
    white-space: nowrap;
    letter-spacing: 0.5px;
  }
  .card--front .brand-name { left: 60px; top: 164px; font-size: 42px; }
  .card--back .brand-name { left: 0; right: 0; text-align: center; top: 158px; font-size: 64px; }

  .divider {
    position: absolute; left: 343px; top: 98px;
    width: 1px; height: 198px;
    background: var(--brand-teal);
  }
  .contact { position: absolute; left: 377px; top: 95px; color: var(--text-light); }
  .contact__name {
    color: var(--brand-teal); font-size: 23px; font-weight: 700;
    letter-spacing: 0.4px; line-height: 1;
  }
  .contact__title { font-size: 15.5px; margin-top: 5px; }
  .contact__address { font-size: 15.5px; line-height: 24px; margin-top: 17px; }
  .contact__list { list-style: none; margin-top: 14px; }
  .contact__item {
    display: flex; align-items: center; gap: 8px;
    font-size: 15.5px; height: 27px;
  }
  .contact__icon { width: 13px; height: 13px; flex: none; }
</style>
</head>
<body>
<main class="stage">
  <section class="card card--front" aria-label="Card front">
    <span class="brand-name">KV7 Supply</span>
    <div class="divider"></div>
    <div class="contact">
      <h1 class="contact__name">DANA WHITLOW</h1>
      <p class="contact__title">CEO/Founder</p>
      <p class="contact__address">P.O Box 4127 Harbour Road Name<br>Westvale AB 90210</p>
      <ul class="contact__list">
        <li class="contact__item">
          <svg class="contact__icon" viewBox="0 0 24 24"><path fill="#2b95bd" d="M6.6 10.8a15.1 15.1 0 0 0 6.6 6.6l2.2-2.2c.3-.3.7-.4 1-.2 1.1.4 2.3.6 3.6.6.6 0 1 .4 1 1V20c0 .6-.4 1-1 1A17 17 0 0 1 3 4c0-.6.4-1 1-1h3.5c.6 0 1 .4 1 1 0 1.3.2 2.5.6 3.6.1.3 0 .7-.2 1z"/></svg>
          555.014.0372
        </li>
        <li class="contact__item">
          <svg class="contact__icon" viewBox="0 0 24 24"><rect x="2" y="5" width="20" height="14" fill="#2b95bd"/><path d="M2 5l10 8 10-8" fill="none" stroke="#1c3858" stroke-width="2"/></svg>
          info@kv7supply.com.au
        </li>
        <li class="contact__item">
          <svg class="contact__icon" viewBox="0 0 24 24" fill="none" stroke="#2b95bd" stroke-width="2"><circle cx="12" cy="12" r="10"/><ellipse cx="12" cy="12" rx="4.5" ry="10"/><path d="M2 12h20M4 7h16M4 17h16"/></svg>
          www.kv7supply.com.au
        </li>
      </ul>
    </div>
  </section>

  <section class="card card--back" aria-label="Card back">
    <span class="brand-name">KV7 Supply</span>
  </section>
</main>
</body>
</html>
```